Website front end design for an education nonprofit

This project involves design and development of the website front end (i.e., Web user interface and user experience design) for TAVO Sphere, a nonprofit initiative for developing an online platform for basic English language instruction, especially targeted toward underprivileged, non-native English speaking populations.

More about us: We are a team of educators, researchers and engineers passionate about this cause and would like to invite talented, creative web developers to join us in this effort to create positive social impact! Please send a personal message to the project owner for the executive summary to get more information about our initiative, big picture vision and the team.

TAVO Sphere website front end (UI/UX) design
Our key goals for this project are to develop an impressive Drupal-based front end for our website as well as to find really talented and creative web/UI/UX designers-cum-developers who are experts in the state-of-the-art web technologies, and are passionate about the cause of global online basic education. At the end of this project, we hope to have long term engagement with the selected developer(s) for our future website design and development needs.

Here are some preliminary guidelines on the TAVO Sphere website front end framework as envisioned by us so far. Please note that we would very much encourage creative ideas and mock-ups from the developers.

1. Current platform: Our website prototype back-end uses Drupal CMS (we plan to continue using Drupal CMS) and at the moment, a toy front-end is based on the Drupal Skeleton platform for its simplicity, clean UI and mobile device friendliness. The web developer / designer can choose any Drupal front end as a starting point or come up with a new Drupal template that meets our requirements below. Prior experience and expertise on Drupal would be great.

2. Audience profile: While the primary audience for the website is expected to be young kids (6-10 years) not very familiar with English, the secondary audience also includes adults interested in basic English language skills. So the overall goal is to have simple, uncluttered / clean, elegant and lightweight (think loading time as well as mobile device friendliness) interface that is extremely intuitive and easy to navigate, is artistic and aesthetically appealing to a wide audience (especially the non-native English speaking populations). The most important point is that our target audience should feel welcome with the clean, crisp look and easy, user-centric navigation, and should in no case feel overwhelmed (say with too much text or clutter on the front page).

3. Front page: Here is a currently envisioned preliminary sketch of the website front page (very much open for refinement and improvements)
a. The top “menu bar” part of the landing page will have our organization name and logo along with (or above) the top menu bar with the following links and sub-links
i. “Learn” link with sub-menu of all our content sections (World learning, Basic sentence learning, Classic short stories, Picture Dictionary)
ii. “About” links with information about us (sub-menu entries: About TAVO Sphere, Team, Supporters, Contributors)
iii. “Contribute” link with sub-menu entries Donate, Volunteer
iv. Menu entries towards the right side: “Login / sign up” followed by
v. “Search” with space to enter the search phrase
b. The middle “main page content” part of the page is where we would have entry points to our main content categories. The portion is envisioned to be graphical, with big blocks (images) as links to our content categories. The current categories (to start with) include 1. Word learning, 2. Basic sentence learning, and 3. Classic stories. We welcome creative ideas to represent these content categories in an appealing and elegant way (for example, these content categories could be portrayed as closed double doors that lead to the pages with the content. We would like to have placeholders for appropriate image links to different content categories – we should be able to put appropriate images or change them as we come up with new ideas that would work best with our target audience). The categories would change and grow as our content evolves, hence the core idea is to build a flexible framework that readily allows for expansion as well as customization.
c. The bottom menu / links bar portion of the landing page will have a list of links that are not included at the top. Examples include (with flexibility needed to add more when needed)
i. “Help”: this leads to a new page with FAQ, How to use
ii. “Contact us” link to a web contact form page
iii. “For Teachers” link to a page with information such as how to use, tips, pilot programs,
iv. “Volunteer” link to page with links such as Donate, Volunteer
v. “Contributors” that would link to a page with information about our Artists, Teachers, Writers, Developers etc.
vi. “Jobs” would link to a jobs page
vii. “Blog” would lead to our blog page
viii. “User stories” link to pages with feedback that we obtain from the users about how the content has helped them,
ix. Web 2.0 placeholders for social media (to be added later)

d. The footer of the website should include text “2013 TAVO Sphere, All rights reserved.”

4. The middle block of the front page is the largest in screen real estate and perhaps the most challenging part that requires much creativity and thought on the UI/UX design aspect – the content pages pointed to by the section links on the middle portion of the front page are also being designed.

5. Color preference is towards soft, elegant (think grays, whites, light blues, other light colors) web safe colors. No harsh (too bright, garish) colors.

6. Fonts preference Nice, clean looking fonts (Arial alright) compatible across browsers.

7. Portability and robustness of the front page layout for different platforms should be carefully considered. Although our first launch target platform is PC (where cross browser compatibility is important), this would very soon be followed by mobile devices such as tablets and smartphones given their prevalence across the globe. This mobile friendly design or easy portability to mobile platforms with little work requirement should be considered as a design requirement.

8. Front page as a framework for the complete website: Note that the top and the bottom portions of the front page are envisioned be used as a common template / frame across all the pages of our website – the middle portion would be used to show our content on the other pages of our website.

9. UX: For the UI/UX design, it is critical to keep in mind key qualities such as ease of use, simplicity, elegance and artistic appeal. Some specific points to keep in mind: (1) the major portion of the target audience would be new to English and (2) young children are expected to be the primary audience but we want the website to appeal to adults interested in learning as well, and (3) we need the website to work even with relatively slow Internet speeds (for underdeveloped / developing regions especially), should always be kept in mind. HTML5 compliance ideas are encouraged.

10. Strictly not desired: Typical corporate feel seen in many webpages, blocky graphics, dull and uninviting overall look with no personality, Flash type effects, harsh colors.

11. Creativity and imagination necessary: We would like to reiterate that the designer/developer has complete freedom to re-imagine the front page considering the above requirements and get back with ideas for an inspiring layout that presents the content outlined above in an intuitive format, carefully considering our target audience.

A note: As a rule, we will always make sure that our developers and artists get proper credit for their work and are recognized and acknowledged by everyone visiting our website.

Expected deliverables:
Website design psd files AND coded webpage / Drupal template: the corresponding source code and all the required libraries, images etc would be required with minimal documentation / pointers on how to make changes and customizations.

Interested developers are encouraged to first send us preliminary prototype Design for the front page to get feedback on whether their approach and style is in line with our needs and preferences. We will suggest the developers to proceed further if the team thinks there is some potential for a match (of course, the final determination would be from the pool of shortlisted submissions) – otherwise, in case the team does not see potential for a match with our needs or if we have already received multiple submissions that are comparatively more closely aligned with our vision for the website, we'd prefer to be respectful of the developers’ time and effort by requesting them not to proceed further.

Please consider this effort as your contribution to an important social cause of global and accessible online education and not a commercial enterprise (our passion for making a positive impact is what is driving the TAVO Sphere nonprofit team to undertake this initiative!). We would like to invite you to join us in this effort!

Project Deadline Extended
Reason: Due to requests from interested designers, we are extending the deadline. Looking forward to receiving many other creative designs!

Please see the project brief.

Real Estate

• Please see the project brief.

```html
<!DOCTYPE html>
<html lang="en">
<head>
<meta charset="utf-8">
<title>TAVO Sphere – Online English Learning</title>
<link rel="stylesheet" href="https://fonts.googleapis.com/css2?family=PT+Sans:wght@400;700&display=swap">
<style>
:root{
  --blue:#1ea2d8;
  --blue-dark:#1587b8;
  --heading:#2196c9;
  --ink:#4a4a4a;
  --muted:#777;
  --panel:#3a93b3;
  --footer:#3690b1;
  --footer-bar:#2b7e9e;
  --dark:rgba(20,20,20,.88);
  --red:#e05454;
  --teal:#4b8f9d;
  --orange:#c96a2a;
}
*{box-sizing:border-box;margin:0;padding:0}
html,body{width:958px;height:1200px;overflow:hidden;background:#fff}
body{position:relative;font-family:"PT Sans",Arial,sans-serif;color:var(--ink)}
.abs{position:absolute}
a{color:inherit;text-decoration:none}

/* header */
.site-header{left:0;top:0;width:958px;height:67px;background:#fff}
.brand{left:144px;top:19px;font-size:25px;font-weight:700;color:var(--blue);letter-spacing:-.3px}
.main-nav{top:30px;font-size:8.5px;font-weight:700;color:#444}
.search{left:530px;top:25px;width:148px;height:19px;background:#eee;border:1px solid #ddd;font-size:7px;color:#999;padding:5px 8px}
.search svg{position:absolute;right:6px;top:4px}
.btn{background:var(--blue);color:#fff;font-size:7.5px;text-align:center;border-bottom:2px solid var(--blue-dark)}
.btn-login{left:687px;top:25px;width:59px;height:20px;line-height:18px}
.btn-signup{left:754px;top:25px;width:60px;height:20px;line-height:18px}

/* hero */
.hero{left:0;top:67px;width:958px;height:417px;background:linear-gradient(160deg,#8a9a45 0%,#5d7a2e 35%,#d9cfc4 55%,#7f9a4a 80%,#a7b5c9 100%)}
.slide-arrow{width:50px;height:50px;border-radius:50%;background:rgba(60,60,60,.35)}
.category{top:409px;width:223px;height:69px;background:var(--dark)}
.category h3{position:absolute;left:15px;top:12px;font-size:12.5px;font-weight:400;color:var(--blue);letter-spacing:.2px}
.category p{position:absolute;left:15px;top:34px;width:150px;font-size:7.3px;line-height:12px;color:#fff}
.category .go{position:absolute;right:0;bottom:0;width:45px;height:42px;background:#1d6f92;display:flex;align-items:center;justify-content:center}

/* mission band */
.mission{left:0;top:484px;width:958px;height:84px;background:linear-gradient(#fbfbfb,#ececec)}
.mission h2{position:absolute;left:145px;top:13px;font-size:16.5px;font-weight:400;color:var(--heading)}
.mission p{position:absolute;left:144px;top:38px;width:530px;font-size:8.3px;line-height:15px;color:#444}
.btn-join{left:698px;top:510px;width:116px;height:32px;line-height:30px;font-size:9.5px}

/* welcome */
.welcome-title{left:144px;top:584px;font-size:16.5px;font-weight:400;color:var(--heading)}
.welcome-photo{left:144px;top:614px;width:185px;height:103px;background:linear-gradient(135deg,#d8b3a6,#efe4de 55%,#c9c2c0)}
.welcome-text{left:346px;top:617px;width:176px;font-size:7.2px;line-height:12.4px;color:#666}
.learn-photo{left:541px;top:594px;width:137px;height:123px;background:linear-gradient(135deg,#8b7a5a,#c8a07a 50%,#3a3a3a)}
.learn-panel{left:678px;top:594px;width:136px;height:123px;background:var(--panel);color:#fff;padding:10px 15px}
.learn-panel h3{font-size:12.5px;font-weight:400}
.learn-panel .lead{font-size:7px;margin:4px 0 6px}
.learn-panel li{list-style:none;font-size:6px;line-height:12.3px}
.learn-panel li::before{content:"› ";}
.btn-outline{right:10px;bottom:10px;border:1px solid #fff;font-size:7px;padding:2px 7px}

/* features */
.pager{top:754px;width:13px;height:13px;background:#8fd0ec;color:#fff;font-size:8px;text-align:center;line-height:12px}
.feature{top:756px;width:210px;text-align:center}
.feature .icon{width:92px;height:92px;border-radius:50%;margin:0 auto;display:flex;align-items:center;justify-content:center}
.feature h3{margin-top:10px;font-size:14px;font-weight:400;color:var(--heading)}
.feature p{margin-top:7px;font-size:7.6px;line-height:13.6px;color:#777}
.feature .btn{display:inline-block;margin-top:12px;width:63px;height:18px;line-height:16px;font-size:6.5px}

/* footer */
.site-footer{left:0;top:990px;width:958px;height:180px;background:var(--footer);color:#fff}
.footer-col{position:absolute;top:14px}
.footer-col h4{font-size:8.5px;font-weight:700;margin-bottom:5px}
.footer-col li{list-style:none;font-size:6.3px;line-height:15.2px}
.newsletter-input{width:160px;height:17px;background:#2f7f9c;border-bottom:1px solid #5aa8c4;font-size:6.3px;padding:5px 8px;margin-top:10px}
.btn-send{margin:5px 0 0 110px;width:50px;height:16px;background:#555;font-size:6.5px;text-align:center;line-height:16px}
.social li{display:flex;align-items:center;gap:5px;font-size:7px;line-height:27px}
.social .dot{width:19px;height:19px;border-radius:50%;background:#2b6f8c}
.footer-bar{left:0;top:1170px;width:958px;height:30px;background:var(--footer-bar);color:#fff;font-size:6.3px;padding:11px 146px}
</style>
</head>
<body>

<header class="abs site-header">
  <a class="abs brand" href="#">TAVO Sphere</a>
  <nav>
    <a class="abs main-nav" style="left:338px" href="#">LEARN</a>
    <a class="abs main-nav" style="left:400px" href="#">ABOUT</a>
    <a class="abs main-nav" style="left:462px" href="#">CONTRIBUTE</a>
  </nav>
  <div class="abs search">SEARCH :
    <svg width="12" height="11" viewBox="0 0 12 11"><circle cx="4.5" cy="4.5" r="3.5" fill="none" stroke="#aaa" stroke-width="1.4"/><line x1="7" y1="7" x2="11" y2="10" stroke="#aaa" stroke-width="1.8"/></svg>
  </div>
  <a class="abs btn btn-login" href="#">LOGIN</a>
  <a class="abs btn btn-signup" href="#">SIGNUP</a>
</header>

<section class="abs hero" role="img" aria-label="Photo of a smiling student lying on the grass with a laptop among yellow flowers"></section>
<div class="abs slide-arrow" style="left:79px;top:249px"><svg width="50" height="50"><polyline points="28,18 21,25 28,32" fill="none" stroke="#999" stroke-width="1.2" stroke-dasharray="2 2"/></svg></div>
<div class="abs slide-arrow" style="left:833px;top:249px"><svg width="50" height="50"><polyline points="22,18 29,25 22,32" fill="none" stroke="#999" stroke-width="1.2" stroke-dasharray="2 2"/></svg></div>

<a class="abs category" style="left:144px" href="#">
  <h3>WORD LEARNING</h3><p>Lorem Ipsum is simply dummy text of the printing and typesetting industry.</p>
  <span class="go"><svg width="12" height="16"><polyline points="3,2 9,8 3,14" fill="none" stroke="#fff" stroke-width="2.6"/></svg></span>
</a>
<a class="abs category" style="left:368px" href="#">
  <h3>BASIC SENTENCE LEARNING</h3><p>Lorem Ipsum is simply dummy text of the printing and typesetting industry.</p>
  <span class="go"><svg width="12" height="16"><polyline points="3,2 9,8 3,14" fill="none" stroke="#fff" stroke-width="2.6"/></svg></span>
</a>
<a class="abs category" style="left:592px;width:222px" href="#">
  <h3>CLASSIC STORIES</h3><p>Lorem Ipsum is simply dummy text of the printing and typesetting industry.</p>
  <span class="go"><svg width="12" height="16"><polyline points="3,2 9,8 3,14" fill="none" stroke="#fff" stroke-width="2.6"/></svg></span>
</a>

<section class="abs mission">
  <h2>We are non profit english learning online platform.</h2>
  <p>Lorem Ipsum is simply dummy text of the printing and typesetting industry. Lorem Ipsum has been the industry's standard dummy text ever since the 1500s</p>
</section>
<a class="abs btn btn-join" href="#">JOIN FOR LEARNING</a>

<h2 class="abs welcome-title">Welcome to TAVO Sphere</h2>
<div class="abs welcome-photo" role="img" aria-label="Photo of a cheerful girl studying at a laptop"></div>
<p class="abs welcome-text">Lorem Ipsum is simply dummy text of the printing and typesetting industry. Lorem Ipsum has been the industry's standard dummy text ever since the 1500s, when an unknown printer took a galley of type and scrambled it to make a type specimen book. It has survived not only five centuries, but also the leap into electronic typesetting, remaining essentially unchanged.</p>
<div class="abs learn-photo" role="img" aria-label="Photo of students with headsets in a computer class"></div>
<div class="abs learn-panel">
  <h3>LEARN</h3>
  <p class="lead">Lorem Ipsum is simply dummy...</p>
  <ul><li>WORD LEARNING</li><li>BASIC SENTENCE LEARNING</li><li>CLASSIC SHORT STORIES</li><li>PICTURE DICTIONARY</li></ul>
  <a class="abs btn-outline" href="#">READ MORE</a>
</div>

<span class="abs pager" style="left:783px">‹</span>
<span class="abs pager" style="left:800px">›</span>

<article class="abs feature" style="left:145px">
  <div class="icon" style="background:var(--red)">
    <svg width="40" height="34" viewBox="0 0 40 34"><circle cx="20" cy="7" r="5" fill="#fff"/><path d="M3 12 L20 20 L37 12 L37 26 L20 33 L3 26 Z" fill="#fff"/><path d="M3 12 L20 20 L37 12" fill="none" stroke="var(--red)" stroke-width="2"/></svg>
  </div>
  <h3>For teachers</h3>
  <p>Lorem Ipsum is simply dummy text of the printing and typesetting industry. Lorem Ipsum has been the industry's standard dummy text ever since the 1500s...</p>
  <a class="btn" href="#">READ MORE</a>
</article>
<article class="abs feature" style="left:377px">
  <div class="icon" style="background:var(--teal)">
    <svg width="44" height="44" viewBox="0 0 44 44" fill="none" stroke="#fff" stroke-width="2.4" stroke-linejoin="round"><rect x="4" y="19" width="8" height="19" rx="1"/><path d="M12 21 L19 13 L21 4 Q26 4 25 12 L24 17 L37 17 Q41 18 39 22 Q41 25 38 27 Q40 30 36 32 Q37 37 32 37 L12 37"/></svg>
  </div>
  <h3>Volunteer</h3>
  <p>Lorem Ipsum is simply dummy text of the printing and typesetting industry. Lorem Ipsum has been the industry's standard dummy text ever since the 1500s...</p>
  <a class="btn" href="#">READ MORE</a>
</article>
<article class="abs feature" style="left:610px">
  <div class="icon" style="background:var(--orange)">
    <svg width="52" height="40" viewBox="0 0 52 40"><ellipse cx="20" cy="15" rx="18" ry="12" fill="#fff"/><path d="M8 24 L4 32 L16 26 Z" fill="#fff"/><ellipse cx="34" cy="23" rx="15" ry="10" fill="#fff" stroke="var(--orange)" stroke-width="2"/><path d="M42 30 L48 37 L37 32 Z" fill="#fff"/></svg>
  </div>
  <h3>Contributors</h3>
  <p>Lorem Ipsum is simply dummy text of the printing and typesetting industry. Lorem Ipsum has been the industry's standard dummy text ever since the 1500s...</p>
  <a class="btn" href="#">READ MORE</a>
</article>

<footer class="abs site-footer">
  <div class="footer-col" style="left:145px">
    <h4>WELCOME</h4>
    <ul><li>HELP</li><li>CONTACT US</li><li>FOR TEACHERS</li><li>VOLUNTEER</li><li>CONTRIBUTORS</li><li>JOBS</li><li>BLOG</li><li>USER STORIES</li></ul>
  </div>
  <div class="footer-col" style="left:275px">
    <h4>LEARN</h4>
    <ul><li>WORD LEARNING</li><li>BASIC SENTENCE LEARNING</li><li>CLASSIC SHORT STORIES</li><li>PICTURE DICTIONARY</li></ul>
    <h4 style="margin-top:9px">ABOUT</h4>
    <ul><li>ABOUT TAVO SPHERE</li><li>TEAM</li><li>SUPPORTERS</li><li>CONTRIBUTORS</li></ul>
  </div>
  <div class="footer-col" style="left:432px;top:21px">
    <h4>CONTRIBUTE</h4>
    <ul><li>DONATE</li><li>VOLUNTEER</li></ul>
    <h4 style="margin-top:12px">NEWSLETTER SIGNUP</h4>
    <ul><li>GET OUR RECENT UPDATES THROUGH YOUR EMAIL :</li></ul>
    <div class="newsletter-input">ENTER YOUR EMAIL D :</div>
    <div class="btn-send">SEND</div>
  </div>
  <ul class="footer-col social" style="left:678px;top:8px">
    <li><span class="dot"></span>: CIRCLENOTE</li>
    <li><span class="dot"></span>: CHIRPLINE</li>
    <li><span class="dot"></span>: WORKBRIDGE</li>
  </ul>
</footer>
<div class="abs footer-bar">COPYRIGHT 2013 TAVO SPHERE. ALL RIGHTS RESERVED.</div>

</body>
</html>
```